Cruise Booking Website

Cruise search and booking website

This project is a redesign of a cruise booking website we did a few years ago.

The current website is located here: http://voyage.pylonworks.example/en/

It's not fully functional but gives you ad idea how miserable the old design was.

All the information about cruises, cruise lines, destinations, ports and shore excursions will be similar to http://www.sailquest.example/
Actual search pages (form, results, single result, sailing and cabin selection, ship info, booking) will have EXACTLY the same info as sailquest.example

We like the style of http://harborfleetdesk.example, it's quite modern, good spacing, not overloaded with information. So you can use it as an example of what we like, not what we want as a final result for us. Please, don't copy it. The result should not be possible to resemble the harborfleetdesk.example, because our site has to be unique. This is important!
If you submit a design that clearly reminds another cruise site it will be rejected!

Also the mockup provided is just to give you the basic structure and show what information has to be present on the page. It doesn't mean the layout has to be the same as a mockup. The layout is up to the designer.

I've updated the mockup to be more generic so it doesn't confuse you:
https://files.boxvault.example/s/k7m2qp9wz4hx/Home%20page.png

When you're adding social sharing icons like plazanet/chirpline you have to use chinese ones instead:
https://files.boxvault.example/s/t3nr8vx5lc2e/chinese-social-icons.png
Originals: http://minilk.example/qR7t

We'll start with home page first and after it's approved inner pages can be designed.

I know the cost of the project doesn't look high, but the task is straight forward and doesn't require to be very original, it's better to follow existing design and layout patterns that proved to work well.
That's why I encourage you to choose a template to build the design on top of one of https://themeparlor.example/ themes if it will save the design work, will be easier and faster for you. So it will be more like a customization than a new design from scratch.

Mockups, site map and logo files:
- https://files.boxvault.example/sh/h48dm2rs73fkpw/QvnbW2Xz8e

Website tree:
- https://sheets.papernest.example/document/d/7xPqR2mLw9sTk4VbN8cHj3YzA6eUf5GdKo1iMnBv/edit?usp=sharing
Updates

So far a lot of designs are just copying http://www.harborfleetdesk.example/ - we don't like it!

We like the style of harborfleetdesk.example, it's quite modern, good spacing, not overloaded with information. So you can use it as an example of what we like, not what we want as a final result for us. Please, don't copy it. The result should not be possible to resemble the harborfleetdesk.example, because our site has to be unique. This is important!

Target Market(s)

Chinese travellers

Industry/Entity Type

Build

Requirements
Must have
• * White, blue and red
* Large spacing, not too much information cramped into a small space like sailquest.example or the current website
* More "hidden" info in popups, tabs and so on, so not to many things are visible at the same time
* Compatible with kestrel scaffold styling (for easier coding):
- http://kestrelkit.codeshelf.example/scaffold/index.html
- http://skinmarket.example/
* Feel free to propose to build the design on top of one of https://themeparlor.example/ themes if it will save the design work, will be easier and faster for you

```html
<!DOCTYPE html>
<html lang="en">
<head>
<meta charset="utf-8">
<title>Seawake Cruises – Destinations</title>
<link href="https://fonts.googleapis.com/css2?family=Source+Sans+3:wght@400;600;700&display=swap" rel="stylesheet">
<style>
:root{
  --blue-deep:#0c3f7a;
  --blue:#1560ad;
  --blue-bright:#2f8de0;
  --blue-text:#1a4f8f;
  --navy:#0b2f5c;
  --orange:#f5821f;
  --orange-dark:#e0660a;
  --grey-bg:#e6e8ea;
  --grey-line:#d3d7db;
  --text:#3a3a3a;
  --white:#ffffff;
  --footer:#2d5f97;
  --footer-dark:#24507f;
}
*{box-sizing:border-box;margin:0;padding:0}
html,body{width:943px;height:1200px;overflow:hidden}
body{
  font-family:"Source Sans 3",sans-serif;color:var(--text);
  background:radial-gradient(ellipse 520px 900px at 50% 40%,#d9e7f5 0%,#6f9fd1 45%,#2c64a4 75%,#1b4a86 100%);
  position:relative;
}
.page{position:absolute;left:142px;top:0;width:660px;height:1200px;background:var(--white)}
.abs{position:absolute}

/* header */
.brand{left:10px;top:26px;display:flex;align-items:center;gap:6px}
.brand-mark{width:34px;height:34px;border-radius:50%;background:var(--blue)}
.brand-name{font-size:26px;font-weight:700;color:var(--blue-text);line-height:1}
.brand-url{left:54px;top:58px;font-size:8px;font-weight:700;color:var(--blue-text)}
.account{left:482px;top:12px;font-size:9px;color:var(--blue)}
.account span{margin:0 6px;color:var(--blue)}
.social{left:568px;top:10px;display:flex;gap:4px}
.social i{display:block;width:17px;height:17px;border-radius:3px}
.phone{left:356px;top:40px;display:flex;gap:6px;align-items:center}
.phone-number{font-size:15px;font-weight:700;color:var(--blue);line-height:1}
.phone-note{font-size:12px;color:#333;line-height:1.1}
.search{left:492px;top:51px;width:154px;height:18px;border:1px solid #c8c8c8;border-radius:2px;background:linear-gradient(#f2f2f2,#fff);font-size:7px;color:#777;padding:4px 8px}
.search svg{position:absolute;right:6px;top:4px}

/* nav */
.nav{left:0;top:88px;width:660px;height:26px;display:flex;background:linear-gradient(#1d6fc1,#0f4f98)}
.nav a{display:flex;align-items:center;justify-content:center;color:#fff;font-size:8px;font-weight:700;text-decoration:none;border-right:1px solid rgba(255,255,255,.15)}
.nav a.active{background:linear-gradient(#3f9cea,#2a82d4)}

/* search panel */
.panel{background:linear-gradient(#1e63a8,#144f90);border:2px solid #2d77c2;border-radius:2px;color:#d9e6f5}
.finder{left:14px;top:130px;width:194px;height:275px}
.finder h2{position:absolute;left:16px;top:12px;font-size:18px;font-weight:400;color:#fff}
.finder .rule{position:absolute;left:2px;right:2px;top:37px;height:1px;background:rgba(255,255,255,.2)}
.lbl{position:absolute;font-size:9px;color:#d9e6f5}
.select{position:absolute;height:17px;background:linear-gradient(#f4f4f4,#d8d8d8);border-radius:2px;font-size:7px;color:#333;padding:4px 7px;line-height:1}
.select::after{content:"";position:absolute;right:0;top:0;width:12px;height:100%;border-left:1px solid #bbb;background:linear-gradient(#eee,#d0d0d0)}
.select b{position:absolute;right:3px;top:4px;z-index:1;width:0;height:0;border:3px solid transparent;border-bottom-color:#777;border-top:0}
.select b::after{content:"";position:absolute;left:-3px;top:5px;border:3px solid transparent;border-top-color:#777;border-bottom:0}
.check{position:absolute;left:14px;top:221px;font-size:7px;display:flex;align-items:center;gap:3px}
.check i{width:8px;height:8px;background:#fff;border-radius:1px}
.btn-search{position:absolute;left:14px;top:232px;width:164px;height:26px;background:linear-gradient(#ff9a36,var(--orange-dark));border:1px solid #f7b06a;border-radius:2px;color:#fff;font-size:12px;font-weight:600;display:flex;align-items:center;justify-content:center}

/* newsletter */
.news{left:14px;top:422px;width:194px;height:234px}
.news-photo{position:absolute;left:8px;top:9px;width:178px;height:106px;border:3px solid #fff;background:linear-gradient(160deg,#7fc8e6,#c9b08e 55%,#e7d9c4)}
.news h3{position:absolute;left:16px;top:124px;font-size:10px;font-weight:700;color:#fff}
.news p{position:absolute;left:16px;top:140px;font-size:7px;color:#fff}
.email{position:absolute;left:16px;top:158px;width:168px;height:18px;background:#fff;border-radius:2px;font-size:7px;color:#777;padding:4px 36px}
.subscribe{position:absolute;left:17px;top:186px;width:68px;height:17px;background:var(--navy);border-radius:2px;font-size:7px;color:#fff;display:flex;align-items:center;justify-content:center}
.contest{position:absolute;left:19px;top:212px;font-size:8px;color:#fff}

/* content */
.crumbs{left:231px;top:130px;font-size:8px;color:var(--blue);display:flex;gap:5px;align-items:center}
.hero{left:228px;top:152px;width:416px;height:212px;background:radial-gradient(ellipse at 45% 40%,#2d8be8,#0f3d7a 70%,#0a2a58)}
.hero-bar{position:absolute;left:0;bottom:0;width:100%;height:40px;background:rgba(15,25,45,.82);color:#fff;font-size:16px;font-weight:700;padding:11px 16px}
.tabs{left:228px;top:376px;display:flex;gap:2px}
.tab{width:110px;height:24px;font-size:7px;color:#fff;display:flex;align-items:center;justify-content:center}
.tab.featured{background:linear-gradient(#1f5ea3,#0d4282)}
.tab.all{background:linear-gradient(#ff9a36,var(--orange-dark))}
.grid-area{left:228px;top:400px;width:416px;height:330px;background:var(--grey-bg)}
.dest{position:absolute;width:126px;height:91px;background:#fff;border:1px solid var(--grey-line)}
.dest .ph{position:absolute;left:2px;top:2px;width:120px;height:67px}
.dest span{position:absolute;left:8px;top:74px;font-size:8px;color:var(--blue)}
.more{position:absolute;right:11px;top:312px;font-size:7.5px;color:#444}
.more em{font-style:normal;color:var(--orange);text-decoration:underline}

/* deals */
.deals{left:12px;top:745px;width:637px;height:169px;background:linear-gradient(#e9eef3,#c9d6e3);}
.deals-head{position:absolute;left:0;top:0;width:100%;height:24px;background:linear-gradient(#1d73c6,#0f57a4);color:#fff;font-size:7.5px;display:flex;justify-content:space-between;align-items:center;padding:0 11px 0 13px}
.deals-head u{font-size:7.5px}
.deal{position:absolute;top:37px;width:139px;height:116px;background:#fff;border:1px solid #d8dde2}
.deal .ph{position:absolute;left:3px;top:3px;width:131px;height:74px}
.deal .t{position:absolute;left:8px;top:85px;font-size:7.5px;color:var(--blue-text)}
.deal .p{position:absolute;left:8px;top:100px;font-size:8px;color:var(--orange)}
.arrow{position:absolute;top:84px;width:18px;height:18px;border-radius:50%;background:var(--orange);display:flex;align-items:center;justify-content:center}

/* partners */
.partners-title{left:12px;top:926px;font-size:12px;font-weight:700;color:var(--blue-deep)}
.pager{left:617px;top:928px;display:flex;gap:2px}
.pager i{width:13px;height:12px;background:#c9ccd0;display:flex;align-items:center;justify-content:center}
.partner{position:absolute;top:950px;width:97px;height:49px;border:1px solid #cfd3d7;background:#fff;display:flex;align-items:center;justify-content:center}
.partner i{display:block;width:54px;height:14px;border-radius:2px}

/* footer */
.footer{left:0;top:1016px;width:660px;height:150px;background:var(--footer);color:#fff}
.footer h4{position:absolute;font-size:11px;font-weight:700}
.footer ul{position:absolute;list-style:none;font-size:7px;line-height:14.8px}
.footer p{position:absolute;font-size:8px;line-height:12px}
.foot-logo{position:absolute;left:273px;top:51px;width:66px;height:64px;background:#fff;display:flex;flex-direction:column;align-items:center;justify-content:center;gap:3px}
.foot-logo i{width:24px;height:24px;border-radius:50%;background:var(--blue)}
.foot-logo span{font-size:7px;font-weight:700;color:var(--blue-text)}
.contact-line{position:absolute;left:475px;font-size:8px;display:flex;align-items:center;gap:5px}
.copyright{left:0;top:1166px;width:660px;height:34px;background:var(--footer-dark);color:#fff;font-size:7px;display:flex;align-items:center;justify-content:center}
</style>
</head>
<body>
<div class="page">
  <!-- header -->
  <div class="abs brand"><i class="brand-mark"></i><span class="brand-name">Seawake Cruises</span></div>
  <div class="abs brand-url">www.seawake.example</div>
  <div class="abs account">Sign In<span>|</span>Signup</div>
  <div class="abs social">
    <i style="background:#e5352f"></i><i style="background:#25a6d9"></i><i style="background:#f0a21b"></i><i style="background:#e84444"></i>
  </div>
  <div class="abs phone">
    <svg width="24" height="24" viewBox="0 0 24 24"><circle cx="12" cy="12" r="11" fill="none" stroke="#777" stroke-width="1.3"/><path d="M9 6c-1 1-2 3-1 6s3 5 5 6l2-2-2-2-1 1c-1-1-2-2-2-4l1-1-1-3z" fill="#666"/></svg>
    <div><div class="phone-number">400 555 0188</div><div class="phone-note">Call Us Today!</div></div>
  </div>
  <div class="abs search">SEARCH :
    <svg width="9" height="9" viewBox="0 0 10 10"><circle cx="4" cy="4" r="3" fill="none" stroke="#aaa"/><path d="M6.5 6.5 9 9" stroke="#aaa"/></svg>
  </div>

  <nav class="abs nav">
    <a style="width:69px">HOME</a>
    <a class="active" style="width:93px">DESTINATIONS</a>
    <a style="width:88px">CRUISE LINES</a>
    <a style="width:82px">CRUISE INFO</a>
    <a style="width:64px">DEALS</a>
    <a style="width:102px">ONLINE BOOKING</a>
    <a style="width:86px">CONTACT US</a>
    <a style="width:76px;border-right:0">BLOG</a>
  </nav>

  <!-- finder -->
  <section class="abs panel finder">
    <h2>Find Your Cruise</h2>
    <div class="rule"></div>
    <div class="lbl" style="left:16px;top:46px">Destination</div>
    <div class="select" style="left:16px;top:58px;width:160px">Destination name<b></b></div>
    <div class="lbl" style="left:16px;top:83px">Length</div>
    <div class="lbl" style="left:104px;top:83px">Month</div>
    <div class="select" style="left:16px;top:94px;width:72px">Length Area<b></b></div>
    <div class="select" style="left:104px;top:94px;width:72px"><b></b></div>
    <div class="lbl" style="left:14px;top:120px">Cruise Lines</div>
    <div class="select" style="left:14px;top:131px;width:164px">Any Cruise line<b></b></div>
    <div class="lbl" style="left:14px;top:162px;font-size:11px;color:#fff">Number of Travelers</div>
    <div class="lbl" style="left:16px;top:180px">Age 25+</div>
    <div class="lbl" style="left:104px;top:180px">Age 0 to 24</div>
    <div class="select" style="left:16px;top:190px;width:72px">5<b></b></div>
    <div class="select" style="left:104px;top:190px;width:72px">0<b></b></div>
    <div class="check"><i></i>Check for senior rates</div>
    <div class="btn-search">Search Cruises</div>
  </section>

  <!-- newsletter -->
  <section class="abs panel news">
    <div class="news-photo" role="img" aria-label="Retired couple relaxing in lounge chairs beside a pool"></div>
    <h3>Cruise Deals Newsletter</h3>
    <p>Subscribe to the best Cruise deals Now!</p>
    <div class="email">Email :</div>
    <div class="subscribe">Subscribe</div>
    <div class="contest">Contest Rules</div>
  </section>

  <!-- destinations -->
  <div class="abs crumbs">HOME
    <svg width="5" height="7" viewBox="0 0 5 7"><path d="M1 1l3 2.5L1 6" fill="none" stroke="#1560ad"/></svg>DISTINATIONS</div>
  <div class="abs hero" role="img" aria-label="Blue world map on a glowing grid">
    <div class="hero-bar">EXPLORE THE WORLD</div>
  </div>
  <div class="abs tabs"><div class="tab featured">FEATURED DESTINATIONS</div><div class="tab all">ALL DESTINATIONS</div></div>
  <div class="abs grid-area">
    <div class="dest" style="left:9px;top:10px"><div class="ph" role="img" aria-label="Traveller launching a paper plane against the sky" style="background:linear-gradient(135deg,#e7c7a5,#8fc3e6)"></div><span>Africa</span></div>
    <div class="dest" style="left:145px;top:10px"><div class="ph" role="img" aria-label="Hiker overlooking a blue bay from a cliff" style="background:linear-gradient(#9cc6ea,#2f6fa8 60%,#4b4a44)"></div><span>Africa</span></div>
    <div class="dest" style="left:281px;top:10px"><div class="ph" role="img" aria-label="Travellers in bright jackets on a mountain top" style="background:linear-gradient(#3b7fd0,#c99a3a 70%,#7a3020)"></div><span>Africa</span></div>
    <div class="dest" style="left:9px;top:111px"><div class="ph" role="img" aria-label="Island resort with water villas in a turquoise lagoon" style="background:linear-gradient(#6fb7e3,#26a3b8 55%,#1e6f94)"></div><span>Africa</span></div>
    <div class="dest" style="left:145px;top:111px"><div class="ph" role="img" aria-label="Woman raising her arms towards a blue sky" style="background:linear-gradient(#3d8fe0,#8cc6f0 70%,#8a5a3f)"></div><span>Africa</span></div>
    <div class="dest" style="left:281px;top:111px"><div class="ph" role="img" aria-label="Couple on a bench above a white sandy beach" style="background:linear-gradient(#7a9a6a,#e9e3cf 55%,#4fb7c0)"></div><span>Africa</span></div>
    <div class="dest" style="left:9px;top:212px"><div class="ph" role="img" aria-label="Hammock under a palm tree by the sea" style="background:linear-gradient(#1f7fd6,#69b8ee 60%,#d8cfae)"></div><span>Africa</span></div>
    <div class="dest" style="left:145px;top:212px"><div class="ph" role="img" aria-label="White cruise ship sailing on deep blue sea" style="background:linear-gradient(#2b6fc4,#bcd7ef 55%,#1b4d93)"></div><span>Africa</span></div>
    <div class="dest" style="left:281px;top:212px"><div class="ph" role="img" aria-label="Old stone tower on a green hill under a blue sky" style="background:linear-gradient(#2f7fd8,#9fcff5 60%,#6aa33a)"></div><span>Africa</span></div>
    <div class="more">Can't find your destination? <em>Click here</em> for our full list of cruises</div>
  </div>

  <!-- last minute deals -->
  <section class="abs deals">
    <div class="deals-head"><span>LAST MINUTE DEALS :</span><u>View all last minute deals</u></div>
    <div class="arrow" style="left:1px"><svg width="6" height="8" viewBox="0 0 6 8"><path d="M4.5 1 1.5 4l3 3" fill="none" stroke="#fff" stroke-width="1.5"/></svg></div>
    <div class="deal" style="left:17px"><div class="ph" role="img" aria-label="Family running along a sunny beach" style="background:linear-gradient(#5aa2e0,#bfe0f2 60%,#e2d2b0)"></div><div class="t">3 day cruise to the Bahamas</div><div class="p">¥ 9000</div></div>
    <div class="deal" style="left:172px"><div class="ph" role="img" aria-label="Rocky island rising from turquoise water" style="background:linear-gradient(#1c4fa0,#b28a4d 50%,#1fb2c9)"></div><div class="t">3 day cruise to the Bahamas</div><div class="p">¥ 9000</div></div>
    <div class="deal" style="left:327px"><div class="ph" role="img" aria-label="Busy city beach with hotels and surf" style="background:linear-gradient(#7c9a8a,#d9e6e0 50%,#2aa2b6)"></div><div class="t">3 day cruise to the Bahamas</div><div class="p">¥ 9000</div></div>
    <div class="deal" style="left:482px"><div class="ph" role="img" aria-label="Couple laughing together outdoors" style="background:linear-gradient(135deg,#6a3a1e,#c97a3a 50%,#e9c39a)"></div><div class="t">3 day cruise to the Bahamas</div><div class="p">¥ 9000</div></div>
    <div class="arrow" style="left:617px"><svg width="6" height="8" viewBox="0 0 6 8"><path d="M1.5 1 4.5 4l-3 3" fill="none" stroke="#fff" stroke-width="1.5"/></svg></div>
  </section>

  <!-- partners -->
  <h3 class="abs partners-title">OUR RELIABLE PARTNERS</h3>
  <div class="abs pager">
    <i><svg width="5" height="7" viewBox="0 0 5 7"><path d="M4 1 1.5 3.5 4 6" fill="none" stroke="#fff"/></svg></i>
    <i><svg width="5" height="7" viewBox="0 0 5 7"><path d="M1 1l2.5 2.5L1 6" fill="none" stroke="#fff"/></svg></i>
  </div>
  <div class="partner" style="left:12px"><i style="background:#b02a2a"></i></div>
  <div class="partner" style="left:120px"><i style="background:#1b4aa0"></i></div>
  <div class="partner" style="left:228px"><i style="background:#4a5a6a"></i></div>
  <div class="partner" style="left:336px"><i style="background:#f39a2a"></i></div>
  <div class="partner" style="left:444px"><i style="background:#3a8fd6;width:30px;height:22px;border-radius:50%"></i></div>
  <div class="partner" style="left:552px"><i style="background:#2a6bc4"></i></div>

  <!-- footer -->
  <footer class="abs footer">
    <h4 style="left:21px;top:20px">Useful Pages</h4>
    <ul style="left:21px;top:39px"><li>About Us</li><li>Contact us</li><li>Blog</li><li>FAQ</li><li>Terms of Service</li><li>Payment info</li><li>Reward Points</li></ul>
    <h4 style="left:149px;top:20px">Cruise Infov</h4>
    <ul style="left:150px;top:39px"><li>Cruise news</li><li>Visa</li><li>Honeymoon cruises</li><li>Firsttime on a Cruise</li></ul>
    <h4 style="left:272px;top:24px">About seawake.example</h4>
    <div class="foot-logo"><i></i><span>Seawake</span></div>
    <p style="left:352px;top:55px;width:95px">We're the most advanced cruise booking providr in china.</p>
    <h4 style="left:475px;top:24px">Contact Us</h4>
    <p style="left:475px;top:46px">Brightkeel Studio, Pte Ltd<br>Harbourview Centre x118, Lantern Ave 7<br>Portmere 20931 Calvera</p>
    <div class="contact-line" style="top:90px"><svg width="11" height="8" viewBox="0 0 11 8"><path d="M1 3c0-2 9-2 9 0v1H7V3H4v1H1z M3 4h5l1 3H2z" fill="#fff"/></svg>(100) 555-0142 - (100) 555-0143</div>
    <div class="contact-line" style="top:107px"><svg width="10" height="8" viewBox="0 0 10 8"><rect x="0.5" y="0.5" width="9" height="7" fill="#fff"/><path d="M0.5 0.5 5 4.5 9.5 0.5" fill="none" stroke="#2d5f97"/></svg>hello@seawake.example</div>
  </footer>
  <div class="abs copyright">© 2013. seawake.example. All rights reserved.</div>
</div>
</body>
</html>
```